Industrial B2B Company Seeks Complete Redesign

We manufacture solid/liquid filtration equipment for manufacturers of chemicals, pharmaceuticals and mining products. We will be redesigning our website; our current design is outdated, and a more modern look is desired. Navigation can be improved. Call to action on the header, such as "Start Here". Video on home page. Designer should incorporate colors from our logo, at least the blues, the brown/gold is optional. Existing website can be found at www.BrindleSeparators.com. Also, we do not make water filters and references to water or water-like images should be avoided.
Number of Pages Required
1 page
Look and feel
Each slider illustrates characteristics of the customer's brand and the style your logo design should communicate.

```html
<!DOCTYPE html>
<html lang="en">
<head>
<meta charset="utf-8">
<title>Brindle Separators, Inc. — Liquid Filtration</title>
<link href="https://fonts.googleapis.com/css2?family=Inter:wght@300;400;500;600;700&display=swap" rel="stylesheet">
<style>
  :root {
    --navy: #0f2a4d;
    --navy-deep: #0a1f3d;
    --blue: #1f4f8f;
    --blue-mid: #2d5fa0;
    --sky: #dce9f7;
    --sky-soft: #eef4fb;
    --text: #2b3647;
    --muted: #5a6678;
    --line: #c9d6e6;
    --white: #ffffff;
  }
  * { box-sizing: border-box; margin: 0; padding: 0; }
  html, body { width: 1200px; height: 2444px; overflow: hidden; }
  body { font-family: "Inter", Arial, sans-serif; color: var(--text); background: var(--white); position: relative; }

  /* Header */
  .site-header { position: absolute; top: 0; left: 0; width: 1200px; height: 64px; display: flex; align-items: center; padding: 0 60px; z-index: 5; }
  .brand { display: flex; align-items: center; gap: 8px; font-size: 13px; font-weight: 600; color: var(--blue); }
  .brand-dot { width: 14px; height: 14px; border-radius: 50%; background: var(--blue); }
  .main-nav { position: absolute; left: 420px; display: flex; gap: 34px; font-size: 12px; font-weight: 500; color: var(--navy); letter-spacing: .04em; }
  .header-cta { position: absolute; right: 60px; display: flex; align-items: center; gap: 8px; font-size: 12px; font-weight: 600; color: var(--navy); letter-spacing: .04em; }

  /* Hero */
  .hero { position: absolute; top: 0; left: 0; width: 1200px; height: 620px; background: linear-gradient(180deg, var(--sky-soft) 0%, var(--sky) 70%, #e6eff9 100%); overflow: hidden; }
  .hero-wave { position: absolute; bottom: 0; left: 0; }
  .hero-title { position: absolute; top: 212px; width: 100%; text-align: center; font-size: 66px; font-weight: 500; color: var(--navy); letter-spacing: .01em; }
  .hero-sub { position: absolute; top: 340px; width: 100%; text-align: center; font-size: 30px; font-weight: 400; line-height: 1.35; color: var(--navy); }
  .hero-button { position: absolute; top: 528px; left: 528px; width: 144px; height: 52px; background: var(--navy); color: var(--white); font-size: 13px; font-weight: 700; letter-spacing: .06em; display: flex; align-items: center; justify-content: center; }

  /* Welcome */
  .welcome { position: absolute; top: 640px; left: 0; width: 1200px; text-align: center; }
  .welcome-kicker { font-size: 28px; font-weight: 400; color: var(--navy); }
  .welcome-title { font-size: 56px; font-weight: 500; color: var(--navy); margin-top: 4px; }
  .welcome-tagline { font-size: 28px; font-weight: 400; color: var(--navy); margin-top: 10px; }
  .welcome-copy { width: 840px; margin: 34px auto 0; font-size: 16px; line-height: 1.65; color: var(--text); }

  /* Innovation band */
  .innovation { position: absolute; top: 1010px; left: 0; width: 1200px; height: 800px; }
  .innovation-title { position: absolute; top: 320px; left: 144px; font-size: 56px; font-weight: 300; line-height: 1.25; color: var(--white); letter-spacing: .01em; }
  .innovation-copy { position: absolute; top: 420px; left: 620px; width: 460px; font-size: 15px; line-height: 1.6; color: #dfe8f5; }

  /* Expertise */
  .expertise-title { position: absolute; top: 1810px; width: 100%; text-align: center; font-size: 46px; font-weight: 600; line-height: 1.2; color: var(--navy); }
  .expertise-grid { position: absolute; top: 1960px; left: 160px; width: 888px; display: grid; grid-template-columns: repeat(4, 222px); grid-template-rows: 160px 200px; }
  .expertise-cell { text-align: center; padding-top: 30px; border-right: 1px solid var(--line); border-bottom: 1px solid var(--line); }
  .expertise-cell:nth-child(4n) { border-right: none; }
  .expertise-cell:nth-child(n+5) { border-bottom: none; padding-top: 40px; }
  .expertise-cell h3 { font-size: 22px; font-weight: 500; color: var(--navy); line-height: 1.2; }
  .expertise-cell p { font-size: 13px; color: var(--muted); line-height: 1.5; margin-top: 14px; }
  .expertise-cell.is-featured { background: linear-gradient(180deg, var(--blue) 0%, var(--navy-deep) 100%); }
  .expertise-cell.is-featured h3, .expertise-cell.is-featured p { color: var(--white); }
</style>
</head>
<body>

<section class="hero">
  <svg class="hero-wave" width="1200" height="200" viewBox="0 0 1200 200" aria-hidden="true">
    <path d="M0 200 L0 150 C 300 200, 600 60, 900 80 C 1050 90, 1130 40, 1200 30 L1200 200 Z" fill="#ffffff"/>
  </svg>
  <h1 class="hero-title">BRINDLE SEPARATORS, INC.</h1>
  <p class="hero-sub">Liquid Filtration: Exceptional Quality,<br>Unparalleled Performance</p>
  <a class="hero-button">START HERE</a>
</section>

<header class="site-header">
  <div class="brand"><span class="brand-dot"></span>Brindle Separators</div>
  <nav class="main-nav">
    <span>HOME</span><span>PRODUCT &amp; SERVICES</span><span>ABOUT</span><span>CONTACT US</span>
  </nav>
  <div class="header-cta">
    <svg width="14" height="14" viewBox="0 0 14 14" aria-hidden="true"><circle cx="7" cy="7" r="6" fill="none" stroke="#0f2a4d" stroke-width="1.5"/><path d="M5 4 L9 7 L5 10" fill="none" stroke="#0f2a4d" stroke-width="1.5"/></svg>
    START HERE
  </div>
</header>

<section class="welcome">
  <p class="welcome-kicker">welcome to</p>
  <h2 class="welcome-title">Brindle Separators</h2>
  <p class="welcome-tagline">Your Partner in Solid-Liquid Separation</p>
  <p class="welcome-copy">At Brindle Separators, we've been setting the standard in liquid filtration for nearly a century. As a leading manufacturer, we pride ourselves on crafting high-quality, long-lasting filtration equipment tailored to meet the unique needs of our customers. With each of our products our goal is to provide you with unwavering reliability, predictability, superior service and exceptional returns on your investment that span decades.</p>
</section>

<section class="innovation">
  <svg width="1200" height="800" viewBox="0 0 1200 800" aria-hidden="true" style="position:absolute;top:0;left:0">
    <defs>
      <radialGradient id="bandGlow" cx="0.38" cy="0.5" r="0.7">
        <stop offset="0" stop-color="#4a7cc0"/>
        <stop offset="0.55" stop-color="#1d4a88"/>
        <stop offset="1" stop-color="#0a1f3d"/>
      </radialGradient>
    </defs>
    <path d="M0 90 C 250 10, 500 10, 700 60 C 900 110, 1050 130, 1200 40 L1200 760 C 1000 800, 800 720, 600 740 C 350 770, 150 800, 0 770 Z" fill="url(#bandGlow)"/>
  </svg>
  <h2 class="innovation-title">INNOVATION<br>PIONEERS</h2>
  <p class="innovation-copy">Our legacy is one of innovation. Almost a century ago, Brindle Separators pioneered the first modern-style horizontal plate filter, introduced the first residential and field-use filters, and even revolutionized the cooking oil filtration process. These and countless other groundbreaking innovations have defined our iconic status and continue to fuel our passion for solving filtration challenges.</p>
</section>

<h2 class="expertise-title">ENGINEERING EXPERTISE<br>AT YOUR SERVICE</h2>

<div class="expertise-grid">
  <div class="expertise-cell"><h3>~100 years</h3><p>unparalleled history<br>of expertise</p></div>
  <div class="expertise-cell is-featured"><h3>Engineering<br>Expertise</h3><p>in industrial<br>liquid filtration</p></div>
  <div class="expertise-cell"><h3>Best<br>Solutions</h3><p>for your<br>unique challenges</p></div>
  <div class="expertise-cell"><h3>Customized<br>Approach</h3><p>Brindle works closely<br>with you</p></div>
  <div class="expertise-cell"><h3>Optimal<br>Solutions</h3><p>developed for<br>your needs</p></div>
  <div class="expertise-cell"><h3>Application<br>Goals</h3><p>tailored solutions<br>for all applications</p></div>
  <div class="expertise-cell"><h3>Dedicated<br>Support</h3><p>ready to deliver<br>the best results</p></div>
  <div class="expertise-cell"><h3>Commitment</h3><p>to your success<br>and satisfaction</p></div>
</div>

</body>
</html>
```